Harborline Auto LLC

Car Dealer Customer Service
Address: 2874 Cresthaven Road, Shelbyville, TN 37162
web: www.harborlineautoxq.net
email: harborlineautoxq@mailnest.example
Phone: (931) 555-0148
Phone: (629) 555-0173

```html
<!DOCTYPE html>
<html lang="en">
<head>
<meta charset="utf-8">
<title>Harborline Auto – Business Card</title>
<link href="https://fonts.googleapis.com/css2?family=Poppins:wght@400;600;700&display=swap" rel="stylesheet">
<style>
  :root {
    --bg: #2b2b2d;
    --card-dark: #232326;
    --card-dark-2: #1c1c1f;
    --paper: #f1f1f0;
    --gold: #e5a93a;
    --blue: #2a7ab0;
    --text-light: #e6e6e6;
    --emboss: #141416;
  }
  * { margin: 0; padding: 0; box-sizing: border-box; }
  html, body { width: 1200px; height: 1138px; overflow: hidden; }
  body {
    background: var(--bg);
    font-family: "Poppins", sans-serif;
    position: relative;
  }
  .card {
    position: absolute;
    border-radius: 14px;
    overflow: hidden;
  }
  /* Front */
  .card-front {
    left: 274px; top: 186px; width: 622px; height: 374px;
    background: linear-gradient(160deg, var(--card-dark), var(--card-dark-2));
  }
  .front-brand {
    position: absolute; left: 0; right: 0; top: 150px;
    text-align: center;
    font-weight: 700; font-size: 36px; letter-spacing: 1px;
    color: var(--emboss);
  }
  .front-web {
    position: absolute; left: 0; right: 0; top: 331px;
    display: flex; justify-content: center; align-items: center; gap: 22px;
    color: var(--text-light); font-size: 15px;
  }
  .front-web .rule { width: 54px; height: 2px; background: var(--gold); }

  /* Back */
  .card-back {
    left: 276px; top: 608px; width: 618px; height: 374px;
    background: var(--card-dark);
  }
  .card-back svg.panel { position: absolute; inset: 0; }
  .person { position: absolute; left: 26px; top: 42px; }
  .person-name { color: var(--gold); font-weight: 700; font-size: 23px; line-height: 1.2; }
  .person-title { color: var(--text-light); font-size: 15.5px; line-height: 1.3; }

  .brand {
    position: absolute; left: 330px; width: 270px; top: 78px;
    display: flex; flex-direction: column; align-items: center; gap: 20px;
  }
  .brand-dot { width: 120px; height: 120px; border-radius: 50%; background: var(--blue); }
  .brand-name { color: var(--blue); font-weight: 700; font-size: 22px; letter-spacing: 0.5px; white-space: nowrap; }

  .contacts { position: absolute; left: 26px; top: 226px; list-style: none; }
  .contacts li { display: flex; align-items: center; gap: 10px; height: 22px; color: var(--text-light); font-size: 15.5px; }
  .contacts li.phone { color: var(--blue); font-weight: 700; font-size: 16.5px; }
  .contacts svg { width: 14px; height: 14px; flex: none; fill: var(--gold); }
  .address { position: absolute; left: 26px; top: 324px; color: var(--text-light); font-size: 15.5px; }
</style>
</head>
<body>
  <section class="card card-front">
    <div class="front-brand">HARBORLINE AUTO</div>
    <div class="front-web"><span class="rule"></span><span>www.harborlineautoxq.net</span><span class="rule"></span></div>
  </section>

  <section class="card card-back">
    <svg class="panel" width="618" height="374" viewBox="0 0 618 374">
      <path d="M300,0 C262,90 270,210 380,258 Q470,292 618,282 L618,0 Z" fill="var(--gold)" transform="translate(-8,6)"/>
      <path d="M300,0 C262,90 270,210 380,258 Q470,292 618,282 L618,0 Z" fill="var(--paper)"/>
    </svg>

    <div class="person">
      <div class="person-name">Daniel Marsh</div>
      <div class="person-title">Managing Director</div>
    </div>

    <div class="brand">
      <div class="brand-dot"></div>
      <div class="brand-name">HARBORLINE AUTO</div>
    </div>

    <ul class="contacts">
      <li class="phone"><svg viewBox="0 0 24 24"><path d="M6.6 10.8a15 15 0 0 0 6.6 6.6l2.2-2.2a1 1 0 0 1 1-.25 11.4 11.4 0 0 0 3.6.57 1 1 0 0 1 1 1V20a1 1 0 0 1-1 1A17 17 0 0 1 3 4a1 1 0 0 1 1-1h3.5a1 1 0 0 1 1 1c0 1.25.2 2.45.57 3.57a1 1 0 0 1-.25 1z"/></svg>931-555-0148</li>
      <li class="phone"><svg viewBox="0 0 24 24"><path d="M6.6 10.8a15 15 0 0 0 6.6 6.6l2.2-2.2a1 1 0 0 1 1-.25 11.4 11.4 0 0 0 3.6.57 1 1 0 0 1 1 1V20a1 1 0 0 1-1 1A17 17 0 0 1 3 4a1 1 0 0 1 1-1h3.5a1 1 0 0 1 1 1c0 1.25.2 2.45.57 3.57a1 1 0 0 1-.25 1z"/></svg>629-555-0173</li>
      <li><svg viewBox="0 0 24 24"><path d="M2 5h20v14H2z M4 7v.5l8 5 8-5V7l-8 5z" fill-rule="evenodd"/></svg>www.harborlineautoxq.net</li>
      <li><svg viewBox="0 0 24 24"><circle cx="12" cy="12" r="10"/></svg>harborlineautoxq@mailnest.example</li>
    </ul>
    <div class="address">2874 Cresthaven Road, Shelbyville, TN 37162</div>
  </section>
</body>
</html>
```